Music Studio and Store Business Card and Logo Design

We need a business card and logo design for an existing Music Studio (Piano and Voice) which will soon expand to offer retail sheet music for all instruments including voice. The expanding store will not sell or lease instruments. We are a well known Fine Arts Studio for instruction to children, college students, and adults with 42 enrolled students and a wait list. We want something with simple elegance, but not archaic. Even a sleek modern look is okay. We do not want something childish or too fun looking because we do serve ages 5 - 62. We would also like the logo workable/transferable to signage for our new location opening in March. We like classic burgundy, black, deep blues, but are open to other suggestions. We included our studio brochure so you can get to know us a little better and some images we thought were interesting with the use of clef signs for the & and using note heads for the bottom or top of the letter "H"

Target Market(s)

All ages

Industry/Entity Type

Business

Contact Information for Business Card

H&H Music StudioPlattsburgh, NYWanda J. Haby and Oren M. Castaldi, Owners

Requirements
Must have
• Phone Number: (555) 817-4062
• Website: www.rbtonalartsroom.example
Nice to have
• Email: lorna@rbtonalartsroom.example
Should not have
• Any instruments on the card other than piano. Instrument pix is not a necessity.

```html
<!DOCTYPE html>
<html lang="en">
<head>
<meta charset="utf-8">
<title>R&amp;B Music Studio – Business Card</title>
<link rel="stylesheet" href="https://fonts.googleapis.com/css2?family=Questrial&family=Source+Sans+3:wght@400;700&display=swap">
<style>
  :root {
    --stage: #141414;
    --card-white: #ffffff;
    --card-grey: #767676;
    --tab-grey: #767676;
    --ink: #111111;
    --ink-soft: #333333;
  }
  * { margin: 0; padding: 0; box-sizing: border-box; }
  html, body {
    width: 1200px;
    height: 900px;
    overflow: hidden;
    background: var(--stage);
  }
  .stage {
    position: relative;
    width: 1200px;
    height: 900px;
    font-family: "Source Sans 3", sans-serif;
  }
  .card {
    position: absolute;
    top: 170px;
    width: 347px;
    height: 561px;
  }
  .card--front { left: 259px; background: var(--card-white); }
  .card--back  { left: 631px; background: var(--card-grey); }

  .tab {
    position: absolute;
    left: 101px;
    width: 144px;
    height: 30px;
    background: var(--tab-grey);
  }
  .tab--top { top: 0; }
  .tab--bottom { bottom: 0; height: 28px; }

  .wordmark {
    position: absolute;
    left: 0;
    width: 100%;
    text-align: center;
    font-family: "Questrial", sans-serif;
    font-weight: 400;
    color: var(--ink);
  }
  .wordmark__initials { display: block; }
  .wordmark__name { display: block; }

  .card--front .wordmark { top: 118px; }
  .card--front .wordmark__initials {
    font-size: 80px;
    line-height: 96px;
    letter-spacing: 2px;
  }
  .card--front .wordmark__name {
    font-size: 40px;
    line-height: 48px;
  }

  .card--back .wordmark { top: 198px; }
  .card--back .wordmark__initials {
    font-size: 132px;
    line-height: 160px;
    letter-spacing: 4px;
  }

  .owners {
    position: absolute;
    top: 324px;
    left: 0;
    width: 100%;
    text-align: center;
    color: var(--ink);
  }
  .owners__name {
    font-weight: 700;
    font-size: 19px;
    line-height: 26px;
  }
  .owners__role {
    font-weight: 400;
    font-size: 15px;
    line-height: 22px;
    color: var(--ink-soft);
  }
  .contact {
    position: absolute;
    top: 423px;
    left: 0;
    width: 100%;
    text-align: center;
    font-size: 15px;
    line-height: 22px;
    color: var(--ink-soft);
  }
  .contact__location { margin-bottom: 10px; }
</style>
</head>
<body>
  <main class="stage">
    <section class="card card--front">
      <div class="tab tab--top"></div>
      <h1 class="wordmark">
        <span class="wordmark__initials">R&amp;B</span>
        <span class="wordmark__name">Music Studio</span>
      </h1>
      <div class="owners">
        <p class="owners__name">Lorna P. Quist</p>
        <p class="owners__name">Oren M. Castaldi</p>
        <p class="owners__role">Owners</p>
      </div>
      <div class="contact">
        <p class="contact__location">Lakemont, NY</p>
        <p class="contact__phone">(555) 817-4062</p>
        <p class="contact__web">www.rbtonalartsroom.example</p>
      </div>
      <div class="tab tab--bottom"></div>
    </section>

    <section class="card card--back">
      <p class="wordmark"><span class="wordmark__initials">R&amp;B</span></p>
    </section>
  </main>
</body>
</html>
```